One Thumbnail for Online Shop for SlideDeck Templates needed

We are selling SlideDeck Templates and need therefore a thumbnail for our online shop.

You can use a stock photo, mock-ups or other design elements.

Format:
squared like 500 x 500
or wide like 1280 x 720

If you want to use a title, use:

"Graphs" ---> Title
"SlideDeck template" ---> subtitle

Attachments:
- OLD: Our old thumbnail which I do not like
- Template: SlideDeck pictures which you can use ( you can also copy them if you need more than these)
- Example: Some examples I found from other shops (please do not copy them exactly, only to show what I mean)

I received lots of designs until now but many are not what I have expected

Target Market(s)

E-Commerce

Industry/Entity Type

Shop

Font styles to use
Sans Serif

Requirements
Should not have
• Do NOT re-design one of the template.png (these are only examples, I will replace them later)

```html
<!DOCTYPE html>
<html lang="en">
<head>
<meta charset="utf-8">
<title>SlideDeck Template 1 – Shop Thumbnail</title>
<link rel="stylesheet" href="https://fonts.googleapis.com/css2?family=Questrial&family=Montserrat:wght@800&display=swap">
<style>
  :root {
    --page: #ffffff;
    --photo-warm: #c97a52;
    --photo-haze: #d9cfc8;
    --photo-light: #f3efec;
    --photo-desk: #e4e2e0;
    --slide-deep: #1d3567;
    --slide-mid: #2d4f8f;
    --slide-light: #3f67a8;
    --slide-pale: #f4f5f8;
    --slide-text: #ffffff;
    --slide-subtext: #dfe6f3;
    --title-gold: #f6b93b;
  }
  * { margin: 0; padding: 0; box-sizing: border-box; }
  html, body {
    width: 1200px;
    height: 1189px;
    overflow: hidden;
    background: var(--page);
  }
  .thumbnail {
    position: relative;
    width: 1200px;
    height: 1189px;
    background: var(--page);
  }
  .scene-photo {
    position: absolute;
    left: 32px;
    top: 28px;
    width: 1132px;
    height: 1140px;
    background:
      radial-gradient(ellipse at 8% 12%, var(--photo-warm) 0%, rgba(201,122,82,0) 45%),
      radial-gradient(ellipse at 90% 20%, #b9b3b0 0%, rgba(185,179,176,0) 50%),
      linear-gradient(180deg, var(--photo-haze) 0%, var(--photo-light) 70%, var(--photo-desk) 100%);
  }
  .slide-screen {
    position: absolute;
    left: 143px;
    top: 258px;
    width: 961px;
    height: 582px;
    overflow: hidden;
  }
  .slide-backdrop {
    position: absolute;
    inset: 0;
    background: linear-gradient(170deg, var(--slide-deep) 0%, var(--slide-mid) 50%, var(--slide-light) 64%, var(--slide-pale) 78%, var(--slide-pale) 100%);
  }
  .slide-title {
    position: absolute;
    left: 80px;
    top: 140px;
    font-family: "Questrial", sans-serif;
    font-size: 43px;
    line-height: 52px;
    color: var(--slide-text);
    font-weight: 400;
  }
  .slide-subtitle {
    position: absolute;
    left: 80px;
    top: 282px;
    font-family: "Questrial", sans-serif;
    font-size: 22px;
    line-height: 25px;
    color: var(--slide-subtext);
  }
  .product-label {
    position: absolute;
    left: 32px;
    width: 1132px;
    top: 1042px;
    text-align: center;
    font-family: "Montserrat", sans-serif;
    font-weight: 800;
    font-size: 50px;
    letter-spacing: 4px;
    color: var(--title-gold);
    text-transform: uppercase;
  }
</style>
</head>
<body>
  <main class="thumbnail">
    <div class="scene-photo" role="img" aria-label="Stock photo of a laptop on a desk in a softly lit office"></div>

    <section class="slide-screen">
      <div class="slide-backdrop" role="img" aria-label="Template slide background with blue tones above and a white lower area"></div>
      <h2 class="slide-title">Lorem ipsum dolor sit<br>amet consetetur</h2>
      <p class="slide-subtitle">Sed diam nonumy eirmod tempor<br>invidunt ut labore et dolore</p>
    </section>

    <h1 class="product-label">SlideDeck Template 1</h1>
  </main>
</body>
</html>
```